Gymnastics and fitness web design

Valdrey Gymnastics and fitness centre is opening a new branch in the United States.
Target Audience:
22 to 40 year old people who are not satisfied with their current body figure, shape and size.
and
Our programs
VoltaRig, Sports performance and personal training
DESIGN STYLE:
We want the site to be trendy, edgy and cool. The colors we prefer are blue, black and silver. Th idea is people should get motivated by seeing our website. We don't like adding many text in the design, images oriented design is what we are after.
Contents should be added-
Slider
who we are?
section for our programs
Why us?
Video showing some tutorials
Articles
contact us form with map, Address, Phone number, timings, and social media buttons.

```html
<!DOCTYPE html>
<html lang="en">
<head>
<meta charset="UTF-8">
<title>Valdrey Gymnastics &amp; Fitness Centre – About</title>
<link href="https://fonts.googleapis.com/css2?family=Montserrat:wght@400;500;600;700&family=Russo+One&display=swap" rel="stylesheet">
<style>
  :root {
    --blue: #2b43e6;
    --blue-deep: #1d33d9;
    --black: #000000;
    --ink: #0b0b0e;
    --white: #ffffff;
    --bar-grey: #e4e4e4;
    --text-grey: #555555;
    --body-text: #e6e6ea;
    --tile-grey: #bdbdbd;
  }
  * { box-sizing: border-box; margin: 0; padding: 0; }
  html, body { width: 1200px; height: 1200px; overflow: hidden; background: var(--black); }
  body { position: relative; font-family: "Montserrat", sans-serif; color: var(--white); }
  .abs { position: absolute; }
  .display { font-family: "Russo One", sans-serif; letter-spacing: 0.08em; text-transform: uppercase; }

  /* top info bar */
  .info-bar { left: 0; top: 0; width: 1200px; height: 34px; background: var(--bar-grey); }
  .info-item { top: 8px; font-size: 7px; line-height: 8px; color: var(--text-grey); font-weight: 500; }
  .info-sep { top: 6px; width: 1px; height: 22px; background: #c4c4c4; }
  .btn-appointment { left: 792px; top: 5px; width: 150px; height: 23px; background: var(--blue); border-radius: 2px;
    font-size: 8.5px; font-weight: 700; color: var(--white); display: flex; align-items: center; justify-content: center; letter-spacing: 0.02em; }

  /* navigation */
  .nav-bar { left: 0; top: 34px; width: 1200px; height: 76px; background: var(--black); }
  .brand-name { left: 254px; top: 50px; font-family: "Russo One", sans-serif; font-size: 28px; color: var(--blue); letter-spacing: 0.02em; line-height: 30px; }
  .brand-tag { left: 255px; top: 81px; font-size: 8px; font-weight: 500; letter-spacing: 0.1em; color: var(--white); }
  .nav-link { top: 63px; font-size: 11px; font-weight: 600; color: var(--white); }
  .nav-link.is-active { left: 665px; top: 58px; width: 65px; height: 24px; border: 1px solid var(--blue); border-radius: 2px;
    display: flex; align-items: center; justify-content: center; }

  /* hero */
  .hero-photo { left: 0; top: 110px; width: 1200px; height: 946px;
    background: radial-gradient(ellipse 380px 520px at 830px 520px, #4a3a32 0%, #2a221f 45%, #0d0c0d 100%); }
  .section-title { font-size: 27px; color: var(--white); }
  .accent-bar { height: 6px; background: var(--blue); }
  .copy { font-size: 10.4px; line-height: 15.6px; color: var(--body-text); }

  /* program card */
  .program-card { left: 252px; top: 392px; width: 344px; height: 425px; background: var(--blue); }
  .program-frame { left: 233px; top: 408px; width: 344px; height: 426px; border: 1px solid var(--white); }
  .program-item { left: 288px; font-size: 18.5px; color: #e9ecff; }

  /* features */
  .feature-icon { left: 656px; width: 40px; height: 40px; }
  .feature-title { left: 717px; font-size: 12px; color: var(--white); }
  .feature-text { left: 718px; width: 230px; font-size: 10.4px; line-height: 15.6px; color: var(--body-text); }

  .programs-heading { left: 0; width: 1205px; top: 937px; text-align: center; font-size: 24px; }
  .programs-sub { left: 0; width: 1205px; top: 977px; text-align: center; font-size: 12px; font-weight: 600; }

  /* program tiles */
  .tile { top: 1056px; width: 300px; height: 144px; }
  .tile-blue { background: linear-gradient(180deg, #2a44ee 0%, #1d36df 100%); }
  .tile-grey { background: linear-gradient(180deg, #c9c9c9 0%, #a9a9a9 100%); }
  .tile-frame { left: 610px; top: 1064px; width: 280px; height: 150px; border: 1px solid #222; }
  .tile-label { left: 600px; width: 300px; top: 1158px; text-align: center; font-size: 24px; line-height: 30px; color: var(--blue); }
</style>
</head>
<body>

  <!-- top info bar -->
  <div class="abs info-bar"></div>
  <div class="abs info-item" style="left:256px;">Monday - Friday 13:30 - 17:30<br>Saturday and Sunday closed</div>
  <div class="abs info-sep" style="left:382px;"></div>
  <div class="abs info-item" style="left:404px;">0222 555 0148<br>info@valdreygfc.com</div>
  <div class="abs info-sep" style="left:509px;"></div>
  <div class="abs info-item" style="left:535px;">Lorem ipsum dolor sit amet, consectetur adipiscing<br>elit. Sed semper massa sit amet</div>
  <div class="abs btn-appointment">MAKE AN APPOINTMENT</div>

  <!-- navigation -->
  <div class="abs nav-bar"></div>
  <div class="abs brand-name">VALDREY</div>
  <div class="abs brand-tag">GYMNASTICS &amp; FITNESS CENTRE</div>
  <div class="abs nav-link" style="left:616px;">Home</div>
  <div class="abs nav-link is-active">About</div>
  <div class="abs nav-link" style="left:751px;">Programs</div>
  <div class="abs nav-link" style="left:838px;">Blog</div>
  <div class="abs nav-link" style="left:900px;">Contact</div>

  <!-- hero -->
  <div class="abs hero-photo" role="img" aria-label="Dark photo of a blonde athlete seen from behind in a sports top"></div>

  <h1 class="abs display section-title" style="left:254px; top:183px;">Why choose Valdrey</h1>
  <div class="abs accent-bar" style="left:254px; top:236px; width:72px;"></div>
  <p class="abs copy" style="left:256px; top:266px; width:398px;">Lorem ipsum dolor sit amet, consectetur adipisicing elit, sed do eiusmod tempor incididunt ut labore et dolore magna aliqua. Ut enim ad minim veniam, quis nostrud exercitation ullamco laboris nisi ut aliquip ex ea commodo consequat. Duis aute irure dolor in reprehenderit in voluptate velit esse cillum dolore eu fugiat nulla pariatur. Excepteur sint occaecat cupidatat non proident, sunt in</p>

  <!-- program card -->
  <div class="abs program-card" role="img" aria-label="Blue-toned photo of a sprinting athlete"></div>
  <div class="abs program-frame"></div>
  <div class="abs display program-item" style="top:560px;">Program one</div>
  <div class="abs display program-item" style="top:610px;">Program two</div>
  <div class="abs display program-item" style="top:658px;">Program three</div>
  <div class="abs display program-item" style="top:707px;">Program four</div>

  <svg class="abs" style="left:290px; top:796px;" width="60" height="132" viewBox="0 0 60 132" aria-hidden="true">
    <line x1="30" y1="0" x2="30" y2="130" stroke="#fff" stroke-width="1.2"/>
    <polyline points="3,102 30,130 57,102" fill="none" stroke="#fff" stroke-width="1.2"/>
  </svg>

  <!-- about -->
  <h2 class="abs display section-title" style="left:656px; top:410px;">About Valdrey</h2>
  <div class="abs accent-bar" style="left:656px; top:464px; width:72px;"></div>
  <p class="abs copy" style="left:656px; top:495px; width:324px;">Lorem ipsum dolor sit amet, consectetur adipisicing elit, sed do eiusmod tempor incididunt ut labore et dolore magna aliqua. Ut enim ad minim veniam, quis nostrud exercitation ullamco laboris nisi ut aliquip ex ea commodo consequat. Duis aute irure dolor in</p>

  <svg class="abs feature-icon" style="top:601px;" viewBox="0 0 40 40" aria-hidden="true" fill="none" stroke="#2b43e6" stroke-width="1.6">
    <circle cx="20" cy="20" r="16"/><ellipse cx="20" cy="20" rx="7" ry="16"/><line x1="4" y1="20" x2="36" y2="20"/><line x1="7" y1="12" x2="33" y2="12"/><line x1="7" y1="28" x2="33" y2="28"/>
  </svg>
  <div class="abs display feature-title" style="top:604px;">Lorem ipsum</div>
  <p class="abs feature-text" style="top:624px;">Lorem ipsum dolor sit amet, consectetur adipisicing elit, sed do eiusmod tempor</p>

  <svg class="abs feature-icon" style="top:677px;" viewBox="0 0 40 40" aria-hidden="true" fill="none" stroke="#2b43e6" stroke-width="1.6">
    <rect x="5" y="5" width="30" height="32" rx="5"/><circle cx="20" cy="13" r="6"/><line x1="20" y1="13" x2="22" y2="10"/>
  </svg>
  <div class="abs display feature-title" style="top:674px;">Lorem ipsum</div>
  <p class="abs feature-text" style="top:693px;">Lorem ipsum dolor sit amet, consectetur adipisicing elit, sed do eiusmod tempor</p>

  <svg class="abs feature-icon" style="top:744px;" viewBox="0 0 40 40" aria-hidden="true" fill="none" stroke="#2b43e6" stroke-width="1.8">
    <path d="M20 35 C8 25 4 19 4 13 C4 8 8 5 12 5 C16 5 18 8 20 11 C22 8 24 5 28 5 C32 5 36 8 36 13 C36 19 32 25 20 35Z"/>
  </svg>
  <div class="abs display feature-title" style="top:745px;">Lorem ipsum</div>
  <p class="abs feature-text" style="top:764px;">Lorem ipsum dolor sit amet, consectetur adipisicing elit, sed do eiusmod tempor</p>

  <svg class="abs feature-icon" style="top:812px;" viewBox="0 0 40 40" aria-hidden="true" fill="none" stroke="#2b43e6" stroke-width="1.6">
    <path d="M9 2 C12 10 12 16 10 22 C9 27 8 31 9 38"/><path d="M31 2 C28 10 28 16 30 22 C31 27 32 31 31 38"/><path d="M11 28 L20 33 L29 28"/><line x1="20" y1="33" x2="20" y2="38"/>
  </svg>
  <div class="abs display feature-title" style="top:810px;">Lorem ipsum</div>
  <p class="abs feature-text" style="top:832px;">Lorem ipsum dolor sit amet, consectetur adipisicing elit, sed do eiusmod tempor</p>

  <!-- our programs -->
  <h2 class="abs display programs-heading">Our programs</h2>
  <p class="abs programs-sub">Lorem ipsum dolor sit amet, consectetur adipiscing elit. Sed semper massa sit amet</p>

  <div class="abs tile tile-blue" style="left:0;" role="img" aria-label="Blue-toned photo of an athlete from behind"></div>
  <div class="abs tile tile-blue" style="left:300px; background:linear-gradient(180deg,#2640ea 0%,#1a32dc 100%);" role="img" aria-label="Blue-toned photo of a male athlete"></div>
  <div class="abs tile tile-grey" style="left:600px;" role="img" aria-label="Greyscale photo of a woman training with battle ropes"></div>
  <div class="abs tile-frame"></div>
  <div class="abs display tile-label">Program<br>three</div>
  <div class="abs tile tile-blue" style="left:900px;" role="img" aria-label="Blue-toned photo of a runner outdoors"></div>

</body>
</html>
```